Group training gym/bootcamp needs a web design

We need a website for our gym that is based in Sydney. We have indoor functional training classes and outdoor bootcamp classes. We would like the web site to have a video (to be created) and photo gallery. I would like the site made on word press and i would like to be able to make minor changes such as changing images and text without having to use a designer.

The website should have the following pages: home page; the gym; the bootcamp; photo gallery; about us; contact.

I have uploaded our logo and i would like to keep to these colour (blue,yellow,silver) and black is also allowed

Target Market(s)

18-50 male and female

Industry/Entity Type

Gym

Coding

Coded - Design and coding required

Number of Pages Required

5+ page

Font styles to use
Sans Serif

Colors
0692cd
fbed22
1b1b1b
e8e8e8

Requirements
Must have
• The website should have the following pages: home page; the gym; the bootcamp; photo gallery; about us; contact.
• I have uploaded our logo and i would like to keep to these colour (blue,yellow,silver) and black is also allowed
• Video upload and photo upload

```html
<!DOCTYPE html>
<html lang="en">
<head>
<meta charset="utf-8">
<title>Core Forge Station</title>
<link rel="stylesheet" href="https://fonts.googleapis.com/css2?family=Roboto:wght@400;500;700&family=Open+Sans:ital,wght@0,400;0,600;0,700;1,400&display=swap">
<style>
:root{
  --blue:#0692cd;
  --yellow:#fbed22;
  --black:#1b1b1b;
  --silver:#e8e8e8;
  --white:#ffffff;
  --text:#555555;
  --heading:#111111;
  --social-1:#1b4f8a;
  --social-2:#1da1f2;
  --social-3:#c8232c;
  --social-4:#c2611c;
}
*{box-sizing:border-box;margin:0;padding:0}
html,body{width:1200px;height:2632px;overflow:hidden}
body{position:relative;background:var(--white);font-family:"Open Sans",Arial,sans-serif;color:var(--text)}
.abs{position:absolute}
.heading{font-family:"Roboto",Arial,sans-serif;font-weight:700;color:var(--heading)}

/* header */
.site-header{left:0;top:0;width:1200px;height:120px;background:linear-gradient(#ffffff,#eeeeee);border-bottom:1px solid #ddd}
.brand{left:96px;top:28px;display:flex;align-items:center;gap:10px}
.brand-mark{width:40px;height:40px;border-radius:50%;background:var(--blue)}
.brand-name{font-family:"Roboto",Arial,sans-serif;font-weight:700;font-size:20px;color:var(--blue);line-height:1.1;letter-spacing:.5px}
.main-nav{right:110px;top:48px;display:flex;gap:30px;font-size:14px;color:#222}
.main-nav .active{color:var(--blue);font-weight:600}

/* hero */
.hero{left:0;top:120px;width:1200px;height:599px;background:radial-gradient(ellipse at 30% 40%,#6b6158 0%,#3d3732 45%,#1f1c1a 100%)}
.hero-content{left:0;top:120px;width:1200px;height:599px;text-align:center;color:var(--white)}
.hero-title{position:absolute;left:0;top:232px;width:1200px;font-family:"Roboto",Arial,sans-serif;font-weight:500;font-size:33px;color:var(--white)}
.hero-sub{position:absolute;left:0;top:285px;width:1200px;font-size:17px;line-height:21px}
.hero-rule{position:absolute;left:578px;top:343px;width:44px;height:3px;background:var(--yellow)}
.btn{display:inline-block;font-family:"Open Sans",Arial,sans-serif;font-weight:700;font-size:13px;text-transform:uppercase;text-align:center;border-radius:2px}
.btn-solid{position:absolute;left:440px;top:383px;width:153px;height:32px;line-height:32px;background:var(--yellow);color:var(--black)}
.btn-outline{position:absolute;left:607px;top:383px;width:152px;height:32px;line-height:28px;border:2px solid var(--yellow);color:var(--yellow)}
.scroll-down{position:absolute;left:575px;top:504px;width:50px;height:50px;border-radius:50%;background:var(--white)}

/* gym */
.section-rule{width:44px;height:3px;background:var(--yellow)}
.gym-title{left:121px;top:748px;font-size:29px}
.gym-intro{left:126px;top:789px;width:400px;font-size:13px;line-height:21px;color:#666}
.feature{left:116px;display:flex;gap:14px}
.feature-icon{width:56px;height:56px;flex:none}
.feature h3{font-family:"Roboto",Arial,sans-serif;font-weight:700;font-size:21px;color:var(--heading);margin-top:-2px}
.feature p{font-size:12.5px;line-height:21px;color:#666;margin-top:6px;width:330px}
.gym-video{left:586px;top:806px;width:496px;height:304px;background:linear-gradient(135deg,#5a4f47,#8a7a6c 50%,#3e3733)}
.play{left:813px;top:931px;width:46px;height:46px}

/* bootcamp */
.bootcamp{left:0;top:1207px;width:1200px;height:505px;background:linear-gradient(90deg,#4a5a3d,#6d7a5a 35%,#4a4a40 70%,#2d3a3f)}
.bootcamp-title{left:0;top:1336px;width:1200px;text-align:center;font-family:"Roboto",Arial,sans-serif;font-weight:700;font-size:27px;color:var(--white)}
.bootcamp-text{left:210px;top:1385px;width:780px;text-align:center;font-size:12.5px;line-height:20px;color:#eee}
.btn-boot{left:541px;top:1494px;width:118px;height:32px;line-height:28px;border:2px solid var(--yellow);color:var(--yellow)}

/* gallery */
.gallery-title{left:0;top:1755px;width:1200px;text-align:center;font-size:29px;font-weight:500}
.card{top:1830px;width:244px;height:232px;background:var(--white);box-shadow:0 2px 4px rgba(0,0,0,.25)}
.card-photo{width:244px;height:175px}
.card-label{height:57px;line-height:57px;text-align:center;font-family:"Roboto",Arial,sans-serif;font-weight:500;font-size:18px;color:var(--heading)}
.gallery-arrows{left:575px;top:2088px;display:flex;gap:22px}

/* partners */
.partners{left:0;top:2130px;width:1200px;height:132px;background:var(--blue)}
.partner{top:2185px;font-family:"Roboto",Arial,sans-serif;font-weight:500;font-size:26px;color:rgba(255,255,255,.9);text-align:center;width:200px}

/* footer */
.footer{left:0;top:2262px;width:1200px;height:335px;background:var(--silver)}
.newsletter-row{left:0;top:2262px;width:1200px;height:98px;border-bottom:1px solid #d2d2d2}
.footer-brand{left:132px;top:2296px;display:flex;align-items:center;gap:10px}
.newsletter-label{left:438px;top:2306px;font-family:"Roboto",Arial,sans-serif;font-weight:500;font-size:17px;color:var(--heading)}
.newsletter-input{left:656px;top:2302px;width:240px;height:30px;background:#f4f4f4;font-size:12px;padding:0 14px;color:#aaa;line-height:30px}
.btn-blue{background:var(--blue);color:var(--white);font-size:11px}
.subscribe{left:902px;top:2302px;width:120px;height:30px;line-height:30px}
.col-title{top:2382px;font-family:"Roboto",Arial,sans-serif;font-weight:700;font-size:22px;color:var(--heading)}
.about-text{left:124px;top:2420px;width:275px;font-size:12px;line-height:20px;font-style:italic;color:#333}
.readmore{left:123px;top:2516px;width:101px;height:28px;line-height:28px}
.links{left:426px;top:2424px;list-style:none;font-size:12px;color:#333;line-height:20.5px}
.links li::before{content:"\203A";margin-right:12px;font-weight:700}
.contact-item{left:655px;display:flex;gap:14px;font-size:12px;line-height:20px;color:#333}
.social{left:897px;display:flex;align-items:center;gap:16px;font-size:12px;color:#333;height:26px}
.social-box{width:26px;height:26px;border-radius:2px;flex:none}
.bottom-bar{left:0;top:2597px;width:1200px;height:35px;background:var(--black);color:#ddd;font-size:11px;text-align:center;line-height:35px}
.bottom-tag{right:52px;top:0;font-size:10px;color:#bbb}
</style>
</head>
<body>

<header class="site-header abs">
  <div class="brand abs">
    <span class="brand-mark"></span>
    <span class="brand-name">CORE FORGE<br>STATION</span>
  </div>
  <nav class="main-nav abs">
    <span class="active">Home</span><span>The Gym</span><span>The Bootcamp</span><span>Photo Gallery</span><span>About us</span><span>Contact us</span>
  </nav>
</header>

<section class="hero abs" role="img" aria-label="Photo of a woman lifting a barbell in a gym class, dimmed"></section>
<div class="hero-content abs">
  <svg class="abs" style="left:558px;top:130px" width="84" height="84" viewBox="0 0 84 84" fill="none" stroke="#fbed22" stroke-width="5" stroke-linejoin="round">
    <g transform="rotate(-40 42 42)">
      <rect x="10" y="28" width="10" height="28" rx="2"/>
      <rect x="20" y="33" width="8" height="18" rx="2"/>
      <rect x="64" y="28" width="10" height="28" rx="2"/>
      <rect x="56" y="33" width="8" height="18" rx="2"/>
      <line x1="28" y1="42" x2="56" y2="42"/>
    </g>
  </svg>
  <h1 class="hero-title">CORE FORGE STATION</h1>
  <p class="hero-sub">We have indoor functional training classes<br>and outdoor bootcamp classes.</p>
  <div class="hero-rule"></div>
  <a class="btn btn-solid">Get Started Now</a>
  <a class="btn btn-outline">Learn More</a>
  <div class="scroll-down">
    <svg width="50" height="50" viewBox="0 0 50 50"><path d="M18 22 L25 29 L32 22" fill="none" stroke="#1b1b1b" stroke-width="2.5"/></svg>
  </div>
</div>

<div class="section-rule abs" style="left:120px;top:737px"></div>
<h2 class="gym-title heading abs">THE GYM</h2>
<p class="gym-intro abs">Neque porro quisquam est qui dolorem ipsum quia dolor sit amet, consectetur, adipisci velit...</p>

<div class="feature abs" style="top:857px">
  <svg class="feature-icon" viewBox="0 0 56 56"><rect width="56" height="56" fill="#fbed22"/><circle cx="22" cy="18" r="4" fill="none" stroke="#1b1b1b" stroke-width="2"/><path d="M14 38 L42 38 M18 32 L28 26 L38 32" fill="none" stroke="#1b1b1b" stroke-width="2"/></svg>
  <div><h3>TRAINING</h3><p>Lorem Ipsum is simply dummy text of the printing and typesetting industry.</p></div>
</div>
<div class="feature abs" style="top:961px">
  <svg class="feature-icon" viewBox="0 0 56 56"><rect width="56" height="56" fill="#fbed22"/><path d="M14 30 Q14 18 22 18 L22 26 M42 30 Q42 18 34 18 L34 26 M16 34 Q28 44 40 34" fill="none" stroke="#1b1b1b" stroke-width="2"/></svg>
  <div><h3>FITNESS</h3><p>Lorem Ipsum is simply dummy text of the printing and typesetting industry.</p></div>
</div>
<div class="feature abs" style="top:1064px">
  <svg class="feature-icon" viewBox="0 0 56 56"><rect width="56" height="56" fill="#fbed22"/><path d="M28 42 L14 28 Q10 20 18 16 Q24 14 28 20 Q32 14 38 16 Q46 20 42 28 Z" fill="none" stroke="#1b1b1b" stroke-width="2"/><path d="M16 28 L23 28 L26 23 L30 33 L33 28 L40 28" fill="none" stroke="#1b1b1b" stroke-width="2"/></svg>
  <div><h3>HEALTH</h3><p>Lorem Ipsum is simply dummy text of the printing and typesetting industry.</p></div>
</div>

<div class="gym-video abs" role="img" aria-label="Video still of a trainer coaching a woman doing dumbbell raises on a ball"></div>
<svg class="play abs" viewBox="0 0 46 46"><circle cx="23" cy="23" r="23" fill="rgba(255,255,255,.75)"/><path d="M19 15 L31 23 L19 31 Z" fill="#444"/></svg>

<section class="bootcamp abs" role="img" aria-label="Photo of a group doing push-ups outdoors at bootcamp, dimmed"></section>
<div class="section-rule abs" style="left:578px;top:1316px"></div>
<h2 class="bootcamp-title abs">THE BOOTCAMP</h2>
<p class="bootcamp-text abs">Sed ut perspiciatis unde omnis iste natus error sit voluptatem accusantium doloremque laudantium, totam rem aperiam, eaque ipsa quae ab illo inventore veritatis et quasi architecto beatae vitae dicta sunt explicabo. Nemo enim ipsam voluptatem quia voluptas sit aspernatur aut odit aut fugit, sed quia consequuntur magni dolores eos qui ratione voluptatem sequi nesciunt. Neque porro quisquam est, qui dolorem ipsum quia dolor sit amet, consectetur.</p>
<a class="btn btn-boot abs">Read More</a>

<h2 class="gallery-title heading abs">PHOTO GALLERY</h2>
<div class="card abs" style="left:98px"><div class="card-photo" role="img" aria-label="Photo of a class doing planks" style="background:linear-gradient(#5c5956,#3c3a38)"></div><div class="card-label">TRAINING CLASSES</div></div>
<div class="card abs" style="left:352px"><div class="card-photo" role="img" aria-label="Photo of athletes lifting at a red wall" style="background:linear-gradient(#d54a5c,#6a4a48)"></div><div class="card-label">TRAINING CLASSES</div></div>
<div class="card abs" style="left:604px"><div class="card-photo" role="img" aria-label="Photo of a woman lifting a barbell overhead" style="background:linear-gradient(#e4e4e4,#8a6a6a)"></div><div class="card-label">TRAINING CLASSES</div></div>
<div class="card abs" style="left:857px"><div class="card-photo" role="img" aria-label="Photo of a group doing box jumps" style="background:linear-gradient(#dcdcdc,#9a948c)"></div><div class="card-label">TRAINING CLASSES</div></div>
<div class="gallery-arrows abs">
  <svg width="14" height="14" viewBox="0 0 14 14"><path d="M9 2 L4 7 L9 12" fill="none" stroke="#1b1b1b" stroke-width="2"/></svg>
  <svg width="14" height="14" viewBox="0 0 14 14"><path d="M5 2 L10 7 L5 12" fill="none" stroke="#1b1b1b" stroke-width="2"/></svg>
</div>

<section class="partners abs"></section>
<div class="partner abs" style="left:198px">Wavefield</div>
<div class="partner abs" style="left:410px">Marla Hue</div>
<div class="partner abs" style="left:634px">Northwind</div>
<div class="partner abs" style="left:843px">Quill Creative</div>

<footer class="footer abs"></footer>
<div class="newsletter-row abs"></div>
<div class="footer-brand abs">
  <span class="brand-mark"></span>
  <span class="brand-name">CORE FORGE<br>STATION</span>
</div>
<div class="newsletter-label abs">NEWSLETTER SUBSCRIBE</div>
<div class="newsletter-input abs">Enter Email id</div>
<a class="btn btn-blue subscribe abs">Subscribe</a>

<h3 class="col-title abs" style="left:124px">ABOUT US</h3>
<p class="about-text abs">Lorem ipsum dolor sit amet, consectetur adipiscing elit, sed do eiusmod tempor incididunt ut labore et dolore magna aliqua. Ut enim ad minim veniam,</p>
<a class="btn btn-blue readmore abs">Read More</a>

<h3 class="col-title abs" style="left:422px">QUICK LINKS</h3>
<ul class="links abs">
  <li>Home</li><li>The Gym</li><li>The Bootcamp</li><li>Photo Gallery</li><li>About us</li><li>Contact us</li>
</ul>

<h3 class="col-title abs" style="left:655px">CONTACT US</h3>
<div class="contact-item abs" style="top:2430px">
  <svg width="12" height="16" viewBox="0 0 12 16"><path d="M6 0 A6 6 0 0 1 12 6 C12 10 6 16 6 16 C6 16 0 10 0 6 A6 6 0 0 1 6 0 Z" fill="#1b1b1b"/><circle cx="6" cy="6" r="2.2" fill="#e8e8e8"/></svg>
  <span style="font-size:11.5px">Main Store 48 Harbour Row<br>North Bayside</span>
</div>
<div class="contact-item abs" style="top:2490px">
  <svg width="12" height="14" viewBox="0 0 12 14"><path d="M2 1 L5 1 L6 4 L4 5.5 Q5.5 8.5 8 10 L9.5 8 L12 9 L12 12 Q12 13 11 13 Q2 12 1 2 Q1 1 2 1 Z" fill="#1b1b1b"/></svg>
  <span>(555)-210-4837</span>
</div>
<div class="contact-item abs" style="top:2520px">
  <svg width="12" height="14" viewBox="0 0 12 14"><rect x="0" y="3" width="12" height="9" fill="#1b1b1b"/><path d="M0 3 L6 8 L12 3" fill="none" stroke="#e8e8e8" stroke-width="1.2"/></svg>
  <span>info@coreforge.example</span>
</div>

<h3 class="col-title abs" style="left:896px">FOLLOW US</h3>
<div class="social abs" style="top:2423px"><span class="social-box" style="background:var(--social-1)"></span>Groupwall</div>
<div class="social abs" style="top:2460px"><span class="social-box" style="background:var(--social-2)"></span>Shortpost</div>
<div class="social abs" style="top:2497px"><span class="social-box" style="background:var(--social-3)"></span>Ideaboard</div>
<div class="social abs" style="top:2534px"><span class="social-box" style="background:var(--social-4)"></span>Photoreel</div>

<div class="bottom-bar abs">Copyrights © 2017 - All Rights Reserved<span class="bottom-tag abs">M1</span></div>

</body>
</html>
```